Locksmith Business Cards

My father-in-law is in need of new business cards for his locksmith business and I need to impress him. Kindly help me out!

You can see the previous business card attached. It is a family run business in North Wales.

No individual names on the cards.

Key Things to Feature:
- The words "Prompt", "Local", "Reliable" (as you can see under the logo on the website)
- 24h Emergency Service
- Covering All of North Wales, the Wirral and Chester
- The color blue
- A key or a lock would be interesting (similar to the ones that come up when you google locksmith business card)

Optional (only if design includes bullet points, like the example below):
https://imgvaultcdn.net/samples/208314/55172/55172_3904821_208314_image.jpg
- Residential / Commercial / Automotive
- Alarms & Cameras
- Key Cutting & Safes

https://www.brynhafod-locksmiths.co.uk/

Industry/Entity Type

Locksmith

Contact Information for Business Card

01632 960 418
07700 900 362
brynhafodlocksmiths@mailvane.com
Brynhafod Locksmiths, The Willow Barn, 7 Tannery Rd., Llandudno LL99 4QX
www.brynhafod-locksmiths.co.uk

Requirements
Must have
• - The words "Prompt", "Local", "Reliable" (as you can see under the logo on the website)
• - 24h Emergency Service
• - Covering All of North Wales, the Wirral and Chester
Nice to have
• - A key or a lock would be interesting (similar to the ones that come up when you google locksmith business card)

```html
<!DOCTYPE html>
<html lang="en">
<head>
<meta charset="utf-8">
<title>Brynhafod Locksmiths – Business Card</title>
<link href="https://fonts.googleapis.com/css2?family=Oswald:wght@400;600&family=Open+Sans:wght@400;600&display=swap" rel="stylesheet">
<style>
  :root {
    --navy: #1c2761;
    --stripe: #3f55a8;
    --card-white: #fbfbfc;
    --ink-light: #ffffff;
    --rule: rgba(255,255,255,0.35);
    --backdrop: #e6e7ea;
  }
  * { margin: 0; padding: 0; box-sizing: border-box; }
  html, body { width: 1200px; height: 900px; overflow: hidden; background: var(--backdrop); }
  .business-card {
    position: absolute; left: 120px; top: 152px;
    width: 960px; height: 596px;
    display: flex;
    box-shadow: 0 10px 30px rgba(0,0,0,0.18);
  }
  .brand-side {
    width: 418px; height: 100%;
    background: var(--card-white);
    display: flex; flex-direction: column; align-items: center; justify-content: center;
  }
  .brand-lockup { display: flex; align-items: center; gap: 14px; }
  .brand-mark { width: 50px; height: 50px; background: var(--navy); border-radius: 8px; }
  .brand-name {
    font-family: 'Oswald', sans-serif; font-weight: 400;
    color: var(--navy); font-size: 41px; line-height: 1.08; letter-spacing: 0.5px;
  }
  .tagline {
    margin-top: 16px; margin-left: 20px;
    font-family: 'Oswald', sans-serif; font-weight: 600;
    color: var(--navy); font-size: 19px;
  }
  .accent-stripe { width: 8px; height: 100%; background: var(--stripe); }
  .info-side {
    flex: 1; height: 100%; background: var(--navy);
    color: var(--ink-light);
    font-family: 'Open Sans', sans-serif;
    padding: 36px 0 0 38px;
  }
  .info-block { width: 410px; }
  .address { font-size: 23px; line-height: 32px; padding-bottom: 14px; }
  .rule { width: 410px; height: 1px; background: var(--rule); }
  .contact-list { list-style: none; padding: 12px 0 14px; }
  .contact-list li { display: flex; align-items: center; gap: 10px; font-size: 23px; line-height: 32.5px; }
  .contact-list svg { width: 18px; height: 18px; fill: var(--ink-light); flex: none; }
  .coverage { padding: 14px 0 14px; font-size: 23px; line-height: 32px; }
  .coverage .emergency { font-weight: 600; }
  .services { list-style: none; padding-top: 14px; }
  .services li { display: flex; align-items: center; gap: 6px; font-size: 23.5px; line-height: 33px; white-space: nowrap; }
  .services li::before {
    content: ""; width: 13px; height: 13px; border-radius: 50%;
    background: var(--ink-light); flex: none;
  }
</style>
</head>
<body>
  <div class="business-card">
    <section class="brand-side">
      <div class="brand-lockup">
        <span class="brand-mark"></span>
        <div class="brand-name">BRYNHAFOD<br>LOCKSMITHS</div>
      </div>
      <p class="tagline">Prompt. Local. Reliable</p>
    </section>
    <div class="accent-stripe"></div>
    <section class="info-side">
      <div class="info-block">
        <p class="address">Brynhafod Locksmiths,<br>The Willow Barn, 7,<br>Tannery Rd., Llandudno LL99 4QX</p>
        <div class="rule"></div>
        <ul class="contact-list">
          <li><svg viewBox="0 0 24 24"><path d="M3 9c0-3 4-5 9-5s9 2 9 5v2h-5V9H8v2H3z M5 13h14l2 7H3z"/></svg>01632 960 418</li>
          <li><svg viewBox="0 0 24 24"><path d="M7 1h10a2 2 0 0 1 2 2v18a2 2 0 0 1-2 2H7a2 2 0 0 1-2-2V3a2 2 0 0 1 2-2zm0 3v14h10V4zm5 15.5a1.2 1.2 0 1 0 0 2.4 1.2 1.2 0 0 0 0-2.4z"/></svg>07700 900 362</li>
          <li><svg viewBox="0 0 24 24"><path d="M2 5h20v14H2z M3.5 6.5 12 13l8.5-6.5" stroke="#1c2761" stroke-width="1.6"/></svg>brynhafodlocksmiths@mailvane.com</li>
          <li><svg viewBox="0 0 24 24"><circle cx="12" cy="12" r="10"/><path d="M2 12h20M12 2c3 3 3 17 0 20M12 2c-3 3-3 17 0 20" stroke="#1c2761" stroke-width="1.4" fill="none"/></svg>www.brynhafod-locksmiths.co.uk</li>
        </ul>
        <div class="rule"></div>
        <p class="coverage"><span class="emergency">24H EMERGENCY SERVICE</span><br>Covering All of North Wales,<br>the Wirral and Chester</p>
        <div class="rule"></div>
        <ul class="services">
          <li>Residential / Commercial / Automotive</li>
          <li>Alarms &amp; Cameras</li>
          <li>Key Cutting &amp; Safes</li>
        </ul>
      </div>
    </section>
  </div>
</body>
</html>
```